South Florida Real Estate Brokerage Business

The name is LAKE VORISSA REAL ESTATE.
The company is a Real estate realty based in Miami.
Is targeted to Latin American clients.
Must express luxury, and efficiency.
Target clients for properties around 250k to a million +.
Vorissa means Royal in Latin.
Should communicate safety and knowledge of the product and transaction with a tech edge.

The web design needs to be a Social tool, with Friendloop and other media integration of some sort. Needs to have a Show case place, a Search place (MLS listings) with maps and filters.
Needs to reflect luxury but also mixed with a social edge capable of engaging clients or transition them to communicate with the page.
Include the logo from the uploaded files, feel free to change the color or font per webdesign.
This is a Front en design, layout and graphics.
Possible future programming if approved.
I can receive Quotes for the Code part.

Spanish and English speakers living in Latin America and Canada looking for apartments and houses to buy.

Business

• Search area.
Neighbourhood area.
Could be a blog or news area.
Client registration.
Social Plugin
• Social linking to networks.
Log in with friendloop account.
Friendloop Like.

```html
<!DOCTYPE html>
<html lang="en">
<head>
<meta charset="utf-8">
<title>Lake Vorissa Real Estate</title>
<link rel="stylesheet" href="https://fonts.googleapis.com/css2?family=Roboto+Condensed:wght@300;400&family=Open+Sans:wght@400;600;700&display=swap">
<style>
  :root {
    --slate: #464b55;
    --slate-dark: #3c4049;
    --gold: #cfa862;
    --gold-line: #d9b26a;
    --red: #c8282b;
    --white: #ffffff;
    --field-text: #555a62;
    --divider: #5e636c;
    --btn-grey: #b4b4b4;
    --hero-sky: #6b98c4;
    --hero-lawn: #5a7d4e;
  }
  * { box-sizing: border-box; margin: 0; padding: 0; }
  html, body { width: 1200px; height: 1040px; overflow: hidden; }
  body {
    background: var(--slate);
    font-family: "Open Sans", sans-serif;
    color: var(--white);
    position: relative;
  }
  .site-header {
    position: absolute; left: 0; top: 0; width: 1200px; height: 149px;
    border-top: 4px solid var(--gold-line);
    background: linear-gradient(180deg, #4a4f59 0%, var(--slate-dark) 100%);
  }
  .brand {
    position: absolute; left: 106px; top: 18px;
    display: flex; flex-direction: column; align-items: center; width: 172px;
  }
  .brand-mark { width: 60px; height: 60px; border: 1px solid var(--gold); margin-bottom: 9px; }
  .brand-name {
    font-family: "Roboto Condensed", sans-serif; font-weight: 400;
    color: var(--gold); text-align: center;
  }
  .brand-name .line-main { display: block; font-size: 21px; line-height: 22px; letter-spacing: 0.5px; }
  .brand-name .line-sub { display: block; font-size: 13px; line-height: 15px; letter-spacing: 1.5px; }
  .account-links {
    position: absolute; right: 80px; top: 15px;
    font-size: 12px; letter-spacing: 0.8px;
  }
  .main-nav {
    position: absolute; right: 78px; top: 111px; display: flex; gap: 25px;
    font-family: "Roboto Condensed", sans-serif; font-weight: 300; font-size: 16px; letter-spacing: 0.5px;
  }
  .hero {
    position: absolute; left: 0; top: 149px; width: 1200px; height: 605px;
    background: linear-gradient(135deg, var(--hero-sky) 0%, var(--hero-lawn) 100%);
  }
  .search-bar {
    position: absolute; left: 106px; top: 194px; width: 1013px; height: 53px;
    background: rgba(255,255,255,0.75);
  }
  .select {
    position: absolute; top: 12px; height: 31px; background: var(--white);
    border: 1px solid #c9ccd0; color: var(--field-text);
    font-size: 13px; letter-spacing: 1px; padding: 6px 9px;
  }
  .select svg { position: absolute; right: 9px; top: 10px; }
  .btn { position: absolute; top: 13px; height: 29px; font-size: 13px; letter-spacing: 0.8px;
    display: flex; align-items: center; justify-content: center; color: #2f3238; }
  .btn-search { left: 759px; width: 87px; background: var(--gold); }
  .btn-advanced { left: 855px; width: 147px; background: var(--btn-grey); }
  .showcase-caption {
    position: absolute; left: 106px; top: 587px; width: 333px; height: 128px;
    background: rgba(40,36,34,0.55);
  }
  .arrow-btn { position: absolute; top: 12px; width: 36px; height: 36px; background: var(--gold);
    display: flex; align-items: center; justify-content: center; }
  .learn-more { position: absolute; left: 102px; top: 12px; width: 106px; height: 36px;
    background: var(--red); font-weight: 700; font-size: 13px; letter-spacing: 1px;
    display: flex; align-items: center; justify-content: center; }
  .like-btn { position: absolute; left: 277px; top: 11px; width: 48px; height: 20px;
    background: #eceef4; border: 1px solid #c1c7d6; color: #3b5590; font-size: 9px;
    display: flex; align-items: center; justify-content: center; gap: 3px; }
  .like-btn .dot { width: 7px; height: 7px; background: #5f78ab; }
  .caption-title { position: absolute; left: 9px; top: 52px;
    font-family: "Roboto Condensed", sans-serif; font-weight: 300; font-size: 34px; line-height: 35px; letter-spacing: 1.2px; }
  .footer-nav {
    position: absolute; left: 106px; top: 787px; display: flex; font-size: 12px; letter-spacing: 0.7px;
  }
  .footer-nav .sep { color: var(--gold); margin: 0 5px; }
  .social { position: absolute; left: 948px; top: 776px; display: flex; gap: 8px; }
  .social a { width: 37px; height: 37px; background: #2e3138; display: block; }
  .footer-rule { position: absolute; left: 0; top: 813px; width: 1200px; height: 1px; background: var(--divider); }
  .link-column { position: absolute; top: 848px; font-size: 12.5px; line-height: 18px; letter-spacing: 0.9px; list-style: none; }
  .newsletter-title { position: absolute; right: 80px; top: 846px;
    font-family: "Roboto Condensed", sans-serif; font-weight: 300; font-size: 20px; letter-spacing: 0.5px; }
  .field { position: absolute; height: 30px; background: var(--white); color: #9a9ea5;
    font-size: 12.5px; padding: 7px 8px; letter-spacing: 0.4px; }
  .btn-submit { position: absolute; left: 1057px; top: 916px; width: 63px; height: 30px;
    background: var(--gold); font-weight: 700; font-size: 13px; display: flex; align-items: center; justify-content: center; }
</style>
</head>
<body>
  <header class="site-header">
    <div class="brand">
      <div class="brand-mark"></div>
      <div class="brand-name"><span class="line-main">LAKE VORISSA</span><span class="line-sub">REAL ESTATE</span></div>
    </div>
    <div class="account-links">REGISTER | LOGIN</div>
    <nav class="main-nav">
      <span>REAL ESTATE</span><span>RESIDENTIAL</span><span>COMMERCIAL/INDUSTRIES</span><span>MLS LISTING</span>
    </nav>
  </header>

  <section class="hero" role="img" aria-label="Photo of an oceanfront villa terrace with lounge furniture, lawn and beach"></section>

  <form class="search-bar">
    <div class="select" style="left:10px;width:127px">For Sale<svg width="12" height="11"><path d="M0 0H12L6 11Z" fill="#222"/></svg></div>
    <div class="select" style="left:166px;width:267px">Property Type<svg width="12" height="11"><path d="M0 0H12L6 11Z" fill="#222"/></svg></div>
    <div class="select" style="left:462px;width:127px">Min Price<svg width="12" height="11"><path d="M0 0H12L6 11Z" fill="#222"/></svg></div>
    <div class="select" style="left:618px;width:127px">Beds<svg width="12" height="11"><path d="M0 0H12L6 11Z" fill="#222"/></svg></div>
    <div class="btn btn-search">search</div>
    <div class="btn btn-advanced">Advance Search</div>
  </form>

  <div class="showcase-caption">
    <div class="arrow-btn" style="left:10px"><svg width="12" height="20"><path d="M10 2L2 10L10 18" stroke="#fff" stroke-width="2.5" fill="none"/></svg></div>
    <div class="arrow-btn" style="left:56px"><svg width="12" height="20"><path d="M2 2L10 10L2 18" stroke="#fff" stroke-width="2.5" fill="none"/></svg></div>
    <div class="learn-more">Learn More</div>
    <div class="like-btn"><span class="dot"></span>Like</div>
    <div class="caption-title">Fabulos Villa in Miami<br>Best Sea View</div>
  </div>

  <nav class="footer-nav">
    <span>CONTACT</span><span class="sep">|</span><span>ABOUT</span><span class="sep">|</span><span>SITEMAP</span><span class="sep">|</span><span>CAREERS</span><span class="sep">|</span><span>FRANCHISE OPPORTUNITIES</span><span class="sep">|</span><span>SELLER LOGIN</span>
  </nav>
  <div class="social">
    <a href="#" aria-label="Friendloop"></a>
    <a href="#" aria-label="Linkwell"></a>
    <a href="#" aria-label="Chirpline"></a>
    <a href="#" aria-label="Vidstream"></a>
  </div>
  <div class="footer-rule"></div>

  <ul class="link-column" style="left:106px"><li>Nam at risus id ligula</li><li>Donec ut elit et</li><li>Donec quis nibh</li><li>Maecenas eu</li><li>Vestibulum a nulla.</li></ul>
  <ul class="link-column" style="left:372px"><li>Nam at risus id ligula</li><li>Donec ut elit et</li><li>Donec quis nibh</li><li>Maecenas eu</li><li>Vestibulum a nulla.</li></ul>
  <ul class="link-column" style="left:637px"><li>Nam at risus id ligula</li><li>Donec ut elit et</li><li>Donec quis nibh</li><li>Maecenas eu</li><li>Vestibulum a nulla.</li></ul>

  <div class="newsletter-title">JOIN OUR NEWSLETTER</div>
  <div class="field" style="left:854px;top:876px;width:128px">First Name</div>
  <div class="field" style="left:992px;top:876px;width:128px">Last Name</div>
  <div class="field" style="left:854px;top:916px;width:193px">Email</div>
  <div class="btn-submit">Submit</div>
</body>
</html>
```